BrimFalcon Business Cards

We have a defined brand. Please visit our website to get a feel for the product and the color pallets. www.brimfalcon-example.com

We need an updated, world class business card design. (See the attached existing card design). Please utilize BOTH sides of the card as shown and be creative with the layout. I do want the horse head icon to be positioned as it is with the existing card.

The remainder of the layout can be customized and I also want it vertically oriented.

Attached are the logo files and please use the colors as follows:
Green - #A5CE39
Tan - #CDBD99
Black

Feel free to play with the colors.

```html
<!DOCTYPE html>
<html lang="en">
<head>
<meta charset="utf-8">
<title>BrimFalcon Business Cards</title>
<link rel="stylesheet" href="https://fonts.googleapis.com/css2?family=Open+Sans:wght@400;600;700&display=swap">
<style>
  :root {
    --backdrop: #5b5852;
    --card-white: #f1f1f1;
    --brand-green: #8dc23c;
    --brand-green-light: #a5ce39;
    --brand-green-dark: #7cb232;
    --ink: #141414;
    --ink-soft: #1e1e1e;
    --type: "Open Sans", Arial, sans-serif;
  }
  * { box-sizing: border-box; margin: 0; padding: 0; }
  html, body {
    width: 1200px; height: 985px; overflow: hidden;
    background: var(--backdrop);
    font-family: var(--type);
  }
  .canvas {
    position: relative; width: 1200px; height: 985px;
    display: flex; justify-content: center; align-items: center; gap: 90px;
  }
  .card {
    position: relative; width: 400px; height: 700px;
    border-radius: 16px; overflow: hidden;
    box-shadow: 0 18px 40px rgba(0,0,0,.45);
  }

  /* front */
  .card--front { background: var(--card-white); display: flex; flex-direction: column; }
  .front-brand {
    height: 240px; display: flex; align-items: center; justify-content: center; gap: 14px;
  }
  .brand-dot { width: 22px; height: 22px; border-radius: 50%; background: var(--brand-green); }
  .brand-name { font-size: 46px; font-weight: 700; color: var(--ink); letter-spacing: .5px; }
  .front-identity {
    height: 90px; background: var(--ink);
    display: flex; flex-direction: column; align-items: center; justify-content: center;
    color: var(--brand-green);
  }
  .person-name { font-size: 27px; font-weight: 700; letter-spacing: 1px; line-height: 1.1; }
  .person-title { font-size: 20px; font-weight: 400; letter-spacing: 1px; }
  .contact-row { height: 95px; display: flex; }
  .contact-icon { width: 90px; display: flex; align-items: center; justify-content: center; }
  .contact-text {
    flex: 1; display: flex; align-items: center; padding-left: 18px;
    font-size: 18px; letter-spacing: .8px;
  }
  .row--green-icon .contact-icon { background: var(--brand-green); color: var(--ink); }
  .row--green-icon .contact-text { background: var(--ink-soft); color: var(--brand-green); }
  .row--black-icon .contact-icon { background: var(--ink); color: var(--card-white); }
  .row--black-icon .contact-text { background: var(--brand-green); color: var(--ink); }
  .contact-text--small { font-size: 16px; padding-left: 12px; }
  .front-address {
    flex: 1; display: flex; flex-direction: column; align-items: center; justify-content: center;
    font-size: 20px; font-weight: 600; color: var(--ink); letter-spacing: 1px; line-height: 1.2;
  }

  /* back */
  .card--back {
    background: linear-gradient(160deg, var(--brand-green-dark) 0%, var(--brand-green) 45%, var(--brand-green-light) 70%, var(--brand-green) 100%);
  }
  .back-pattern {
    position: absolute; inset: 0;
    background: radial-gradient(ellipse at 40% 55%, rgba(255,255,255,.18), rgba(0,0,0,.06) 70%);
  }
  .back-wordmark {
    position: absolute; left: 50%; top: 50%;
    transform: translate(-50%, -50%) rotate(90deg);
    font-size: 54px; font-weight: 600; color: var(--ink); white-space: nowrap; letter-spacing: 1px;
  }
</style>
</head>
<body>
<main class="canvas">
  <section class="card card--front">
    <header class="front-brand">
      <span class="brand-dot"></span>
      <span class="brand-name">BrimFalcon</span>
    </header>
    <div class="front-identity">
      <p class="person-name">Dale Morven</p>
      <p class="person-title">President &amp; CEO</p>
    </div>
    <div class="contact-row row--green-icon">
      <div class="contact-icon">
        <svg width="48" height="40" viewBox="0 0 48 40" aria-hidden="true">
          <path d="M4 14 Q4 4 24 4 Q44 4 44 14 L36 16 L34 11 L14 11 L12 16 Z" fill="currentColor"/>
          <path d="M14 15 L34 15 L40 26 L40 36 L8 36 L8 26 Z" fill="currentColor"/>
          <g fill="var(--brand-green)">
            <rect x="17" y="21" width="3" height="3"/><rect x="22.5" y="21" width="3" height="3"/><rect x="28" y="21" width="3" height="3"/>
            <rect x="17" y="26" width="3" height="3"/><rect x="22.5" y="26" width="3" height="3"/><rect x="28" y="26" width="3" height="3"/>
          </g>
        </svg>
      </div>
      <div class="contact-text">306.555.0142</div>
    </div>
    <div class="contact-row row--black-icon">
      <div class="contact-icon">
        <svg width="56" height="38" viewBox="0 0 56 38" aria-hidden="true">
          <rect x="3" y="3" width="50" height="32" fill="none" stroke="currentColor" stroke-width="3"/>
          <path d="M3 3 L28 22 L53 3 M3 35 L22 17 M53 35 L34 17" fill="none" stroke="currentColor" stroke-width="3"/>
        </svg>
      </div>
      <div class="contact-text">Dale@BrimFalcon.com</div>
    </div>
    <div class="contact-row row--green-icon">
      <div class="contact-icon">
        <svg width="52" height="52" viewBox="0 0 52 52" aria-hidden="true">
          <circle cx="26" cy="26" r="24" fill="currentColor"/>
          <ellipse cx="26" cy="26" r="24" rx="10" ry="24" fill="none" stroke="var(--brand-green)" stroke-width="2"/>
          <path d="M2 26 H50 M6 14 H46 M6 38 H46" stroke="var(--brand-green)" stroke-width="2"/>
        </svg>
      </div>
      <div class="contact-text contact-text--small">www.brimfalcon-example.com</div>
    </div>
    <footer class="front-address">
      <span>Pinecrest, Saskatchewan</span>
      <span>canada</span>
    </footer>
  </section>

  <section class="card card--back">
    <div class="back-pattern" role="img" aria-label="Faint repeating brand mark pattern across the green card"></div>
    <span class="back-wordmark">BrimFalcon</span>
  </section>
</main>
</body>
</html>
```